Business Card for Professional Photographer

I'm looking for an eye catching modern clean design that compliments my logo/ website fonts & colours.
I specialise in architecture, corporate & commercial photography so I'm marketing to professional clients rather than portrait / wedding clients.

I would prefer to not have a solid black design.

My logo brand guide is as follows :

Main front font. : Reislust
Main font colour : #fff
Slogan front font : Ubuntu Bold
Monogram front font : Venti Medium
Container colour : #fff

I need print ready files in pdf .png & .eps formats.

Included in the files below are some screen grabs as reference to font & colours etc.

```html
<!DOCTYPE html>
<html lang="en">
<head>
<meta charset="utf-8">
<title>Still Angle – Business Card</title>
<link rel="stylesheet" href="https://fonts.googleapis.com/css2?family=Ubuntu:wght@300;500&family=Roboto:wght@400&family=Saira+Semi+Condensed:wght@600&display=swap">
<style>
  :root {
    --backdrop: #bdbdbd;
    --card-dark: #141414;
    --card-light: #f4f4f2;
    --gold: #c79a45;
    --gold-light: #e0bd6a;
    --gold-deep: #a9782e;
    --ink: #2b2b2b;
    --rule: #e2c988;
  }
  * { margin: 0; padding: 0; box-sizing: border-box; }
  html, body { width: 1200px; height: 576px; overflow: hidden; }
  body { background: var(--backdrop); position: relative; font-family: "Roboto", Arial, sans-serif; }

  .card {
    position: absolute;
    border-radius: 8px;
    overflow: hidden;
  }

  /* Front */
  .card--front {
    left: 82px; top: 138px; width: 484px; height: 294px;
    background: var(--card-dark);
  }
  .front__photos {
    position: absolute; inset: 0;
    background: linear-gradient(135deg, #2a2622 0%, #1a1a1a 40%, #23262b 70%, #141414 100%);
  }
  .front__mark {
    position: absolute; left: 66px; top: 98px; width: 82px; height: 82px;
    border: 3px solid var(--gold); border-radius: 6px;
  }
  .front__name {
    position: absolute; left: 182px; top: 118px;
    font-family: "Ubuntu", Arial, sans-serif; font-weight: 300;
    font-size: 23px; letter-spacing: 3px; color: var(--gold-light);
    text-transform: uppercase; white-space: nowrap;
  }
  .front__tagline {
    position: absolute; left: 183px; top: 151px;
    font-family: "Ubuntu", Arial, sans-serif; font-weight: 500;
    font-size: 8px; letter-spacing: 1.6px; color: var(--gold);
    white-space: nowrap;
  }
  .front__url {
    position: absolute; left: 137px; top: 257px;
    font-family: "Ubuntu", Arial, sans-serif; font-weight: 300;
    font-size: 13px; letter-spacing: 2px; color: var(--gold-light);
  }

  /* Back */
  .card--back {
    left: 602px; top: 138px; width: 480px; height: 290px;
    background: var(--card-light);
  }
  .back__logo {
    position: absolute; left: 22px; top: 82px; width: 196px;
    display: flex; flex-direction: column; align-items: center;
  }
  .back__mark {
    width: 84px; height: 84px;
    border: 3px solid var(--gold); border-radius: 6px;
  }
  .back__name {
    margin-top: 16px;
    font-family: "Ubuntu", Arial, sans-serif; font-weight: 300;
    font-size: 16px; letter-spacing: 2.2px; color: var(--gold-deep);
    text-transform: uppercase; white-space: nowrap;
  }
  .back__tagline {
    margin-top: 3px;
    font-family: "Ubuntu", Arial, sans-serif; font-weight: 500;
    font-size: 6px; letter-spacing: 1.1px; color: var(--gold);
    white-space: nowrap;
  }
  .back__divider {
    position: absolute; left: 232px; top: 66px; width: 1px; height: 160px;
    background: linear-gradient(to bottom, transparent, var(--rule) 20%, var(--rule) 80%, transparent);
  }
  .person {
    position: absolute; left: 268px; top: 76px;
  }
  .person__name {
    font-family: "Saira Semi Condensed", Arial, sans-serif; font-weight: 600;
    font-size: 19px; color: var(--gold-deep); line-height: 24px;
  }
  .person__role { font-size: 13px; color: var(--ink); line-height: 18px; }
  .contact {
    position: absolute; left: 268px; top: 137px;
    list-style: none; font-size: 12.5px; color: var(--ink);
  }
  .contact__item { display: flex; align-items: center; height: 18.5px; }
  .contact__icon { width: 10px; height: 10px; margin: 0 14px 0 4px; }
  .contact__address { margin-top: 4px; }
</style>
</head>
<body>

<section class="card card--front">
  <div class="front__photos" role="img" aria-label="Dark collage of architecture, interior and commercial photographs"></div>
  <div class="front__mark"></div>
  <div class="front__name">Still Angle</div>
  <div class="front__tagline">Architecture Corporate Commercial</div>
  <div class="front__url">www.stillangle.com.au</div>
</section>

<section class="card card--back">
  <div class="back__logo">
    <div class="back__mark"></div>
    <div class="back__name">Still Angle</div>
    <div class="back__tagline">Architecture Corporate Commercial</div>
  </div>
  <div class="back__divider"></div>

  <div class="person">
    <div class="person__name">Mark Ellison</div>
    <div class="person__role">Photographer</div>
  </div>

  <ul class="contact">
    <li class="contact__item">
      <svg class="contact__icon" viewBox="0 0 10 10" aria-hidden="true"><path d="M2 1 L4 1 L4.6 3 L3.5 3.8 Q4.6 5.6 6.2 6.5 L7 5.4 L9 6 L9 8 Q5 9 2.4 6 Q0.6 3.6 2 1 Z" fill="var(--gold)"/></svg>
      <span>0400128356</span>
    </li>
    <li class="contact__item">
      <svg class="contact__icon" viewBox="0 0 10 10" aria-hidden="true"><rect x="0.5" y="2" width="9" height="6" fill="var(--gold)"/><path d="M0.5 2 L5 5.5 L9.5 2" fill="none" stroke="var(--card-light)" stroke-width="0.9"/></svg>
      <span>hello@stillangle.com.au</span>
    </li>
    <li class="contact__item">
      <svg class="contact__icon" viewBox="0 0 10 10" aria-hidden="true"><circle cx="5" cy="5" r="4.3" fill="none" stroke="var(--gold)" stroke-width="1"/><ellipse cx="5" cy="5" rx="1.8" ry="4.3" fill="none" stroke="var(--gold)" stroke-width="0.8"/><line x1="0.7" y1="5" x2="9.3" y2="5" stroke="var(--gold)" stroke-width="0.8"/></svg>
      <span>www.stillangle.com.au</span>
    </li>
    <li class="contact__address">8 Harbour Rd Portland Vic 3305</li>
  </ul>
</section>

</body>
</html>
```